Tallowmere Air Business Card Design

Design new, 2 sides, business cards for a residential and light commercial heating, air conditioning contractor.

Target Market(s)

Homeowners, small businesses

Industry/Entity Type

Business

Contact Information for Business Card

Dominic Westerhall
Phone - 862-415-2736
Email
Address - PO box 518
Brightwater NJ 07912
Website - www.HarborBreezeLLC.example

Requirements
Must have
• logo, company colors, standard size with no die cut, so I can use nova stamp

```html
<!DOCTYPE html>
<html lang="en">
<head>
<meta charset="utf-8">
<title>Tallowmere Air Business Card</title>
<link rel="stylesheet" href="https://fonts.googleapis.com/css2?family=Lato:wght@400;700;900&display=swap">
<style>
  :root {
    --bg: #b9b9b9;
    --orange: #f38b34;
    --maroon: #9e2238;
    --red: #c8283a;
    --gold: #f4a21f;
    --charcoal: #2a2829;
    --white: #ffffff;
    --ink: #3a2a20;
    --light: #e9e9e9;
  }
  * { box-sizing: border-box; margin: 0; padding: 0; }
  html, body { width: 1200px; height: 950px; overflow: hidden; }
  body {
    background: radial-gradient(circle at 40% 35%, #d4d4d4, var(--bg) 70%);
    font-family: "Lato", Arial, sans-serif;
    position: relative;
  }
  .card {
    position: absolute;
    width: 700px;
    height: 400px;
    overflow: hidden;
    box-shadow: 0 6px 18px rgba(0,0,0,0.25);
  }
  /* Front side */
  .card-front {
    left: 110px; top: 50px;
    background: var(--orange);
    display: flex; flex-direction: column; align-items: center; justify-content: center;
  }
  .brand {
    display: flex; align-items: center; gap: 14px;
    color: var(--maroon);
    font-weight: 900;
    text-transform: uppercase;
    letter-spacing: 1px;
    white-space: nowrap;
  }
  .brand-mark {
    width: 20px; height: 20px; border-radius: 50%;
    background: var(--maroon);
    flex: none;
  }
  .card-front .brand { font-size: 46px; }
  .card-front .brand-mark { width: 30px; height: 30px; }
  .tagline {
    margin-top: 30px;
    text-align: center;
    color: var(--ink);
    font-size: 19px;
    line-height: 1.35;
  }
  /* Back side */
  .card-back {
    left: 390px; top: 500px;
    background: var(--white);
  }
  .back-shapes { position: absolute; inset: 0; }
  .card-back .brand {
    position: absolute; left: 40px; top: 160px;
    font-size: 27px;
  }
  .person {
    position: absolute; right: 36px; top: 140px;
    text-align: right; color: var(--light);
    font-size: 17px; line-height: 1.45;
  }
  .person-name { color: var(--red); font-size: 21px; text-transform: uppercase; letter-spacing: 0.5px; }
  .person-role { color: var(--gold); font-size: 17px; margin-bottom: 10px; }
  .contacts {
    position: absolute; left: 36px; top: 282px;
    list-style: none; color: var(--light); font-size: 17px;
  }
  .contacts li { display: flex; align-items: center; gap: 12px; height: 25px; }
  .contacts svg { width: 15px; height: 15px; fill: var(--red); flex: none; }
</style>
</head>
<body>
  <section class="card card-front" aria-label="Business card front">
    <div class="brand"><span class="brand-mark"></span>Tallowmere Air</div>
    <p class="tagline">Residential &amp; light commercial heating<br>Air conditioning contractor</p>
  </section>

  <section class="card card-back" aria-label="Business card back">
    <svg class="back-shapes" viewBox="0 0 700 400" width="700" height="400" aria-hidden="true">
      <polygon points="0,262 330,262 395,125 700,125 700,400 0,400" fill="var(--charcoal)"/>
      <polygon points="0,246 140,246 136,256 0,256" fill="var(--maroon)"/>
      <polygon points="150,246 330,246 326,256 146,256" fill="var(--gold)"/>
    </svg>

    <div class="brand"><span class="brand-mark"></span>Tallowmere Air</div>

    <div class="person">
      <div class="person-name">Dominic Westerhall</div>
      <div class="person-role">CEO/Founder</div>
      <div>PO box 518</div>
      <div>Brightwater NJ 07912</div>
      <div>www.TallowmereAirLLC.example</div>
    </div>

    <ul class="contacts">
      <li><svg viewBox="0 0 16 16"><path d="M3 1l3 3-1.5 2a9 9 0 0 0 5.5 5.5L12 10l3 3-2 2C7 15 1 9 1 3z"/></svg>862-415-2736</li>
      <li><svg viewBox="0 0 16 16"><rect x="1" y="3" width="14" height="9" rx="1"/><rect x="5" y="13" width="6" height="2"/></svg>862-415-2791</li>
      <li><svg viewBox="0 0 16 16"><rect x="4" y="1" width="8" height="14" rx="1.5"/></svg>862-415-2805</li>
      <li><svg viewBox="0 0 16 16"><path d="M1 3h14v10H1z M1 3l7 6 7-6" stroke="var(--charcoal)" stroke-width="1"/></svg>info@tallowmereairllc.example</li>
    </ul>
  </section>
</body>
</html>
```